Web Infographic for Life Insurance

We need an infographic for our insurance site based on research commissioned previously. We have a report of statistics on the cost and coverage of life insurance in 1999 vs 2019. What we're looking for is an infographic that presents these statistics in an entertaining and informative way. Site is CoverWren.com
Target Market(s)
Americans ages 30-65 interested in life insurance.
Industry/Entity Type
Insurance
Number of Pages Required
1 page
Font styles to use
Sans Serif
Decorative
Colors
85cae6
faa54b
ffffff
86cfc6
Requirements
Must have
- Long vertical infographic readable on mobile devices
Nice to have
- Footnote references
Should not have
- Extremely small text
- Any brand logos or trademarked imagery other than for coverwren

```html
<!DOCTYPE html>
<html lang="en">
<head>
<meta charset="utf-8">
<title>CoverWren — The Cost and Coverage of Life Insurance in 1999 vs 2019</title>
<link href="https://fonts.googleapis.com/css2?family=Montserrat:wght@400;500;600;700;800&family=Lato:wght@400;700&display=swap" rel="stylesheet">
<style>
:root{
  --sky:#85cae6;
  --sky-deep:#2f8dbd;
  --ocean:#0f5f8e;
  --orange:#faa54b;
  --mint:#86cfc6;
  --white:#ffffff;
  --ink:#1c1c1c;
  --text:#555b61;
  --line:#e6e9ec;
}
*{margin:0;padding:0;box-sizing:border-box}
html,body{width:1200px;height:5093px;overflow:hidden;background:var(--white)}
body{position:relative;font-family:"Lato",sans-serif;color:var(--ink)}
.abs{position:absolute}
.waves{position:absolute;left:0;top:0;width:1200px;height:5093px}
.brand{left:110px;top:26px;font-family:"Montserrat",sans-serif;font-weight:700;font-size:24px;color:var(--white);letter-spacing:.5px}
.phone{left:596px;top:22px;display:flex;align-items:center;gap:14px;font-family:"Montserrat",sans-serif;font-weight:500;font-size:24px;color:var(--white)}
.hero-title{left:110px;top:168px;font-family:"Montserrat",sans-serif;font-weight:800;font-size:54px;line-height:64px;color:var(--white)}
.hero-title .accent{color:var(--orange)}
.hero-art{left:735px;top:285px;width:465px;height:410px;border-radius:40px;background:linear-gradient(135deg,#e9eef8,#c7d3f3 60%,#f0b8b8)}
.card{background:var(--white);box-shadow:0 0 12px rgba(0,0,0,.12);left:110px;width:980px}
.card-title{position:absolute;left:0;width:100%;text-align:center;font-family:"Montserrat",sans-serif;font-weight:500;color:var(--ink)}
.orange{color:var(--orange)}
.stat-box{background:var(--sky);width:240px;height:112px;color:var(--white);font-family:"Montserrat",sans-serif;font-size:13px;line-height:20px;padding:20px 0 0 98px}
.stat-box .val{font-size:16px;margin-top:6px}
.stat-box svg{position:absolute;left:20px;top:26px}
.stat-circle{width:156px;height:156px;border-radius:50%;background:var(--orange);color:var(--white);text-align:center;font-family:"Montserrat",sans-serif;font-size:14px;line-height:22px;padding-top:38px}
.stat-circle .val{font-size:24px;font-weight:600;margin-top:8px}
.mini-stat{display:flex;align-items:center;gap:22px;font-family:"Montserrat",sans-serif}
.mini-stat .ring{width:86px;height:86px;border-radius:50%;border:5px solid #f1f3f5;display:flex;align-items:center;justify-content:center}
.mini-stat .lab{font-size:15px;font-weight:600}
.mini-stat .num{font-size:25px;color:var(--orange);margin-top:8px}
.art{border-radius:24px}
.small-caps{font-family:"Montserrat",sans-serif;font-weight:600;font-size:14px;text-align:center;line-height:22px}
.sec-title{font-family:"Montserrat",sans-serif;font-weight:500;font-size:40px;line-height:44px}
.sec-sub{font-family:"Montserrat",sans-serif;font-weight:600;font-size:13px;line-height:24px;margin-top:18px}
.facts{list-style:none;margin-top:22px}
.facts li{position:relative;padding-left:36px;font-size:13px;line-height:25px;color:var(--text);margin-bottom:22px}
.facts li::before{content:"";position:absolute;left:0;top:6px;width:10px;height:10px;border:2px solid var(--orange);border-radius:50%}
.reasons-title{left:0;width:1200px;text-align:center;font-family:"Montserrat",sans-serif;font-weight:500;font-size:36px;line-height:46px}
.reasons-note{left:0;width:1200px;text-align:center;font-family:"Montserrat",sans-serif;font-weight:600;font-size:13px;line-height:28px}
.reason{width:160px;text-align:center}
.reason .ring{margin:0 auto;width:100px;height:100px;border-radius:50%;border:8px solid var(--orange);box-shadow:0 0 0 3px #fde6cc inset;display:flex;align-items:center;justify-content:center;font-family:"Montserrat",sans-serif;font-size:26px;color:var(--sky)}
.reason .lab{margin-top:22px;font-family:"Montserrat",sans-serif;font-weight:600;font-size:13px;line-height:23px}
.footer{left:0;width:1200px;text-align:center;top:5022px;font-size:13px;color:var(--text)}
</style>
</head>
<body>

<svg class="waves" viewBox="0 0 1200 5093" aria-hidden="true">
  <defs>
    <linearGradient id="heroGrad" x1="0" y1="0" x2="1" y2="1">
      <stop offset="0" stop-color="#9fd6ee"/><stop offset=".5" stop-color="#3f9fcc"/><stop offset="1" stop-color="#0f5f8e"/>
    </linearGradient>
    <linearGradient id="waveGrad" x1="0" y1="0" x2="0" y2="1">
      <stop offset="0" stop-color="#85cae6"/><stop offset="1" stop-color="#0f5f8e"/>
    </linearGradient>
  </defs>
  <path d="M0 0H1200V60C1050 120 980 10 900 120C830 220 700 200 600 330C520 440 470 600 300 640C170 670 80 700 0 735Z" fill="url(#heroGrad)"/>
  <path d="M0 1730C60 1690 160 1690 230 1710L230 1860C150 1800 60 1820 0 1870Z" fill="url(#waveGrad)"/>
  <path d="M1200 2290C1130 2300 1070 2360 1060 2420L1090 2420L1090 2700L1200 2700Z" fill="url(#waveGrad)"/>
  <path d="M0 2640C40 2560 110 2500 160 2470L160 2690H1090V2810H300C180 2830 60 2900 0 2990Z" fill="url(#waveGrad)"/>
  <path d="M1090 3980C1130 3930 1170 3910 1200 3900V4220H1090Z" fill="url(#waveGrad)"/>
  <path d="M640 1550" fill="none"/>
  <path d="M585 590C540 650 520 700 555 760C570 790 560 810 548 820" fill="none" stroke="#c9ccd0" stroke-width="3" stroke-dasharray="10 8"/>
  <path d="M548 1715C530 1750 540 1790 555 1800" fill="none" stroke="#c9ccd0" stroke-width="3" stroke-dasharray="10 8"/>
  <path d="M548 2700C530 2740 545 2770 555 2790" fill="none" stroke="#c9ccd0" stroke-width="3" stroke-dasharray="10 8"/>
  <path d="M548 4230C530 4260 545 4290 555 4300" fill="none" stroke="#c9ccd0" stroke-width="3" stroke-dasharray="10 8"/>
</svg>

<div class="abs brand">COVERWREN</div>
<div class="abs phone">
  <svg width="40" height="40" viewBox="0 0 40 40" aria-hidden="true"><circle cx="20" cy="20" r="18" fill="none" stroke="#fff" stroke-width="2"/><path d="M14 11l4 4-2 3c1 3 3 5 6 6l3-2 4 4-3 3c-7 0-15-8-15-15z" fill="#fff"/></svg>
  1-888-555-0147
</div>
<h1 class="abs hero-title">THE COST AND<br>COVERAGE OF<br><span class="accent">LIFE INSURANCE</span><br>IN 1999 VS 2019</h1>
<div class="abs hero-art art" role="img" aria-label="Isometric illustration of a city of data dashboards and people analysing charts"></div>

<!-- Summary statistics -->
<section class="abs card" style="top:850px;height:860px">
  <h2 class="card-title" style="top:118px;font-size:50px">Summary Statistics</h2>
  <div class="card-title orange" style="top:200px;font-size:34px">1992-1997</div>
  <div class="abs stat-box" style="left:40px;top:355px">
    <svg width="60" height="60" viewBox="0 0 60 60" aria-hidden="true"><circle cx="30" cy="26" r="20" fill="none" stroke="#fff" stroke-width="2"/><circle cx="30" cy="26" r="12" fill="none" stroke="#fff" stroke-width="2"/><path d="M18 42l-6 14 8-3 4 6 5-14M42 42l6 14-8-3-4 6-5-14" fill="none" stroke="#fff" stroke-width="2"/></svg>
    TYPE TERM<br>PREMIUM<div class="val">3.62 (4.91)</div>
  </div>
  <div class="abs stat-circle" style="left:422px;top:333px">LENGTH OF<br>POLICY<div class="val">2.27</div></div>
  <div class="abs stat-box" style="left:725px;top:355px">
    <svg width="60" height="60" viewBox="0 0 60 60" aria-hidden="true"><circle cx="30" cy="26" r="20" fill="none" stroke="#fff" stroke-width="2"/><circle cx="30" cy="26" r="12" fill="none" stroke="#fff" stroke-width="2"/><path d="M18 42l-6 14 8-3 4 6 5-14M42 42l6 14-8-3-4 6-5-14" fill="none" stroke="#fff" stroke-width="2"/></svg>
    REAL AMOUNT<br>OF POLICY<div class="val">132.97 (136.41)</div>
  </div>
  <svg class="abs" style="left:0;top:0" width="980" height="860" aria-hidden="true">
    <g stroke="#a9dcf2" stroke-width="5" fill="#a9dcf2">
      <line x1="305" y1="411" x2="390" y2="411"/><path d="M400 411l-16-9v18z"/>
      <line x1="595" y1="411" x2="690" y2="411"/><path d="M700 411l-16-9v18z"/>
      <line x1="485" y1="500" x2="410" y2="585"/><path d="M402 595l4-19 12 11z"/>
      <line x1="518" y1="500" x2="600" y2="585"/><path d="M608 595l-16-7 12-11z"/>
    </g>
  </svg>
  <div class="abs mini-stat" style="left:195px;top:640px">
    <div class="ring"><svg width="44" height="44" viewBox="0 0 44 44" aria-hidden="true"><circle cx="22" cy="22" r="18" fill="none" stroke="#faa54b" stroke-width="2"/><rect x="9" y="20" width="26" height="6" fill="none" stroke="#faa54b" stroke-width="2"/><line x1="9" y1="35" x2="35" y2="9" stroke="#faa54b" stroke-width="2"/></svg></div>
    <div><div class="lab">NON-SMOKER</div><div class="num">774 (.418)</div></div>
  </div>
  <div class="abs mini-stat" style="left:530px;top:640px">
    <div class="ring"><svg width="44" height="44" viewBox="0 0 44 44" aria-hidden="true"><circle cx="22" cy="16" r="9" fill="none" stroke="#85cae6" stroke-width="2"/><path d="M6 40c2-10 8-14 16-14s14 4 16 14" fill="none" stroke="#faa54b" stroke-width="2"/></svg></div>
    <div><div class="lab">MALE</div><div class="num">774 (.418)</div></div>
  </div>
</section>

<!-- Purchases -->
<section class="abs card" style="top:1830px;height:860px">
  <h2 class="card-title" style="top:66px;font-size:33px;line-height:48px">Number of life insurance policy purchases in the<br><span class="orange">United States</span> from <span class="orange">1998 to 2018</span> (in millions)</h2>
  <div class="abs art" style="left:28px;top:270px;width:245px;height:180px;background:linear-gradient(135deg,#dde7f3,#a9c4de)" role="img" aria-label="Illustration of a team climbing blocks to a goal"></div>
  <div class="abs art" style="left:400px;top:300px;width:230px;height:170px;background:linear-gradient(135deg,#2c8fc8,#0d3f73)" role="img" aria-label="Map of the United States"></div>
  <svg class="abs" style="left:0;top:0" width="980" height="860" aria-hidden="true">
    <g fill="none" stroke="#2a8ad0" stroke-width="5"><path d="M500 190c-10 25-6 45 6 60"/><path d="M290 352c25 18 60 18 85 0"/><path d="M765 362c-20 15-45 15-65 0"/></g>
    <g fill="#2a8ad0"><path d="M510 262l-16-6 12-10z"/><path d="M385 348l-18 0 8 14z"/><path d="M690 352l18-2-7 15z"/></g>
    <g fill="#2a8ad0"><rect x="812" y="412" width="8" height="22"/><rect x="824" y="404" width="8" height="30"/><rect x="836" y="396" width="8" height="38"/><rect x="848" y="386" width="8" height="48"/></g>
  </svg>
  <div class="abs" style="left:730px;top:328px;width:230px;font-family:Montserrat,sans-serif;font-weight:600;font-size:9px;line-height:17px;text-align:center">IN 2018, APPROXIMATELY 27.8 MILLION LIFE INSURANCE POLICIES WERE PURCHASED IN THE UNITED STATES.</div>
  <div class="abs" style="left:730px;top:450px;width:230px;text-align:center;font-family:Montserrat,sans-serif;font-size:25px;color:var(--orange)">27.8</div>
  <div class="abs small-caps" style="left:0;top:545px;width:980px">THE GROWTH OF THE INTERNET HAS REDUCED TERM LIFE<br>PRICES BY <span class="orange">8 - 15</span> PERCENT.</div>
  <div class="abs" style="left:330px;top:640px;width:320px;height:220px;background:linear-gradient(180deg,#f5a6c6,#d64a63 60%,#8a8f98)" role="img" aria-label="Illustration of raised hands holding hearts"></div>
</section>

<!-- Numbers and cost -->
<section class="abs card" style="top:2810px;height:1410px">
  <div class="abs" style="left:53px;top:90px;width:480px">
    <h2 class="sec-title">Life Insurance By<br>The Numbers</h2>
    <p class="sec-sub">LOREM IPSUM DOLOR SIT AMET, CONSECTETUR<br>ADIPISCING ELIT, SED DO EIUSMOD TEMPOR</p>
    <ul class="facts">
      <li>57%&nbsp; Percent of American adults who have life insurance</li>
      <li>32% Of American adults with life insurance, the percent who only have group coverage - which usually isn't enough</li>
      <li>10x to 12x&nbsp; The multiples of your annual income that most financial advisors recommend you need when buying life insurance for income replacement</li>
      <li>50% Percent of life insurance policies are purchased via independent agents</li>
      <li>40% Percent of life insurance policies purchased via affiliated agents (meaning they only sell products for one insurance company)</li>
    </ul>
  </div>
  <div class="abs" style="left:540px;top:215px;width:410px;height:300px;background:linear-gradient(90deg,#3fc6e8,#f97fb0 30%,#8fe36b 50%,#2a8ad0 70%,#fbe066 85%,#f58d5a)" role="img" aria-label="Illustration of a woman presenting a rising colourful bar chart"></div>

  <svg class="abs" style="left:80px;top:850px" width="380" height="420" role="img" aria-label="Bar chart: 20%, 50%, 30%, 25%, 10%">
    <rect x="20" y="180" width="46" height="170" fill="#15a3c4"/><ellipse cx="43" cy="180" rx="23" ry="6" fill="#4cc2dd"/>
    <rect x="86" y="40" width="46" height="310" fill="#5bb463"/><ellipse cx="109" cy="40" rx="23" ry="6" fill="#8ad28f"/>
    <rect x="152" y="110" width="46" height="240" fill="#c0c93c"/><ellipse cx="175" cy="110" rx="23" ry="6" fill="#dde169"/>
    <rect x="218" y="150" width="46" height="200" fill="#fbd33b"/><ellipse cx="241" cy="150" rx="23" ry="6" fill="#fde57e"/>
    <rect x="284" y="250" width="46" height="100" fill="#f2683d"/><ellipse cx="307" cy="250" rx="23" ry="6" fill="#f89878"/>
    <circle cx="43" cy="155" r="12" fill="#1a6b8a"/><rect x="97" y="5" width="24" height="22" fill="#e54b3c"/><rect x="163" y="83" width="24" height="14" fill="#3fa9e0"/><circle cx="241" cy="125" r="11" fill="#f6c315"/><circle cx="307" cy="225" r="12" fill="none" stroke="#e54b3c" stroke-width="4"/>
    <g font-family="Montserrat, sans-serif" font-size="20" fill="#1c1c1c" text-anchor="middle"><text x="43" y="382">20%</text><text x="109" y="382">50%</text><text x="175" y="382">30%</text><text x="241" y="382">25%</text><text x="307" y="382">10%</text></g>
  </svg>
  <div class="abs" style="left:533px;top:775px;width:420px">
    <h2 class="sec-title">Stats About The Cost<br>Of Life Insurance</h2>
    <p class="sec-sub">LOREM IPSUM DOLOR SIT AMET, CONSECTETUR<br>ADIPISCING ELIT, SED DO EIUSMOD TEMPOR</p>
    <ul class="facts">
      <li>6x-10x How much more permanent life insurance costs vs. term life insurance<sup>†</sup></li>
      <li>8% * Average percent increase in your insurance costs as you age, assuming your health stays the same</li>
      <li>30% The average cost difference between sequential health ratings (preferred vs standard, for example)</li>
      <li>2x to 3x How much rates for smokers cost vs. rates for nonsmokers (but a year after you quit smoking, most companies will offer you nonsmoker rates)</li>
      <li>50% The average difference between the least expensive and most expensive rate for the same person across insurance companies</li>
    </ul>
  </div>
</section>

<!-- Top reasons -->
<h2 class="abs reasons-title" style="top:4305px">Top Reasons For Buying <span class="orange">Life Insurance</span><br>In The U.S.</h2>
<p class="abs reasons-note" style="top:4436px">ACCORDING TO A 2019 REPORT FROM TRADE RESEARCH ORGANIZATION LUMERA RESEARCH AND THE NON-PROFIT<br>ORGANIZATION LIFE FORWARD, THESE ARE THE MOST COMMON REASONS AMERICANS SAID THEY BOUGHT LIFE INSURANCE</p>

<div class="abs reason" style="left:110px;top:4560px"><div class="ring">37%</div><div class="lab">INCOME<br>REPLACEMENT</div></div>
<div class="abs reason" style="left:272px;top:4560px"><div class="ring">30%</div><div class="lab">BURIAL/<br>FINAL EXPENSES</div></div>
<div class="abs reason" style="left:436px;top:4560px"><div class="ring">28%</div><div class="lab">28% WEALTH<br>TRANSFER</div></div>
<div class="abs reason" style="left:598px;top:4560px"><div class="ring">27%</div><div class="lab">27% PAY OFF<br>MORTGAGE</div></div>
<div class="abs reason" style="left:762px;top:4560px"><div class="ring">19%</div><div class="lab">19% REPLACED A<br>POLICY</div></div>
<div class="abs reason" style="left:924px;top:4560px"><div class="ring">17%</div><div class="lab">17% TAX ADVANTAGED<br>SAVE/INVEST</div></div>

<div class="abs reason" style="left:193px;top:4785px"><div class="ring">14%</div><div class="lab">14% ESTATE TAXES/<br>LIQUIDITY</div></div>
<div class="abs reason" style="left:355px;top:4785px"><div class="ring">14%</div><div class="lab">14% FUNDS FOR<br>COLLEGE EDUCATION</div></div>
<div class="abs reason" style="left:517px;top:4785px"><div class="ring">13%</div><div class="lab">13% CHARITABLE<br>GIFT</div></div>
<div class="abs reason" style="left:681px;top:4785px"><div class="ring">08%</div><div class="lab">8% SUPPLEMENT<br>GROUP COVERAGE</div></div>
<div class="abs reason" style="left:845px;top:4785px"><div class="ring">08%</div><div class="lab">8% BUSINESS<br>PURPOSES</div></div>

<p class="abs footer">© 2020 CoverWren. All Rights Reserved</p>
</body>
</html>
```